Poster for Kirtan Music Event

Design (3) 24" x 36" Posters

I have provided a sample a friend did in Australia: ( Picture No. 4 )

Use all the text on sample poster except the replacement changes below.

Replace with the following text as this is for different location:
Replacement Text:

Every Friday Night 7:00pm-8:30pm
Kealoha Pilates & Movement Studio
947 Hollister Rd Paia

Free Kirtan Experience! or Free Event
Mohan Priya Sevi & Companions

Optional Text:

A evening of music, singing of spiritual mantras, and refreshments

Bring flowers, musical instruments, friends, or just come with an open heart.

Meditate on transcendental sounds that provide rest for the mind & heart"

An evening of music & singing of sacred mantra's

```html
<!DOCTYPE html>
<html lang="en">
<head>
<meta charset="utf-8">
<title>Kirtan Experience – Poster</title>
<link rel="stylesheet" href="https://fonts.googleapis.com/css2?family=Tillana:wght@500;700&family=Parisienne&display=swap">
<style>
  :root {
    --orange: #f36a1c;
    --orange-light: #f8873a;
    --orange-deep: #e24f12;
    --art-red: #d63a1c;
    --art-red-soft: #e8552a;
    --maroon: #6a1a0c;
    --yellow: #f2d40a;
    --green: #2d5a14;
    --cream: #f6dba8;
    --panel: #f3d79d;
    --panel-edge: #e7c57f;
    --ink: #1c0b05;
  }
  html, body {
    margin: 0;
    padding: 0;
    width: 800px;
    height: 1200px;
    overflow: hidden;
    background: var(--orange);
  }
  .poster {
    position: relative;
    width: 800px;
    height: 1200px;
    overflow: hidden;
    background: radial-gradient(ellipse at 35% 30%, var(--orange-light) 0%, var(--orange) 45%, var(--orange-deep) 100%);
    font-family: "Tillana", cursive;
  }
  .backdrop-art {
    position: absolute;
    left: 30px;
    top: 80px;
    width: 580px;
    height: 900px;
    border-radius: 45% 45% 30% 30%;
    background:
      radial-gradient(ellipse at 50% 62%, var(--art-red) 0%, rgba(214, 58, 28, 0.85) 35%, rgba(232, 85, 42, 0.55) 60%, rgba(243, 106, 28, 0) 82%),
      radial-gradient(ellipse at 45% 20%, rgba(250, 150, 90, 0.55) 0%, rgba(243, 106, 28, 0) 60%);
  }
  .title {
    position: absolute;
    left: 38px;
    top: -12px;
    margin: 0;
    font-size: 150px;
    font-weight: 700;
    line-height: 1;
    color: var(--maroon);
    letter-spacing: 2px;
  }
  .sun-emblem {
    position: absolute;
    left: 604px;
    top: 2px;
    width: 160px;
    height: 160px;
  }
  .shanti {
    position: absolute;
    left: 18px;
    top: 190px;
    font-size: 42px;
    font-weight: 500;
    color: var(--ink);
    line-height: 1;
  }
  .subtitle {
    position: absolute;
    left: 152px;
    top: 160px;
    margin: 0;
    font-size: 100px;
    font-weight: 700;
    color: var(--yellow);
    line-height: 1;
    letter-spacing: 6px;
  }
  .tagline {
    position: absolute;
    left: 40px;
    top: 270px;
    margin: 0;
    font-family: "Parisienne", cursive;
    font-size: 48px;
    line-height: 58px;
    color: var(--maroon);
  }
  .tagline-mantras {
    position: absolute;
    left: 112px;
    top: 386px;
    font-size: 52px;
    font-weight: 700;
    color: var(--green);
    line-height: 1;
  }
  .photo {
    position: absolute;
    border: 2px solid #fff3e0;
    box-shadow: 0 4px 10px rgba(0, 0, 0, 0.35);
  }
  .photo-singer {
    left: 520px;
    top: 250px;
    width: 330px;
    height: 260px;
    transform: rotate(-12deg);
    background: linear-gradient(135deg, #efe6dc 0%, #c9a898 50%, #5a3a30 100%);
  }
  .photo-harmonium {
    left: 585px;
    top: 420px;
    width: 260px;
    height: 270px;
    transform: rotate(-5deg);
    background: linear-gradient(160deg, #b07a40 0%, #d8c0a0 45%, #5b3219 100%);
  }
  .photo-chanting {
    left: 590px;
    top: 715px;
    width: 280px;
    height: 250px;
    transform: rotate(10deg);
    background: linear-gradient(140deg, #3d6a2a 0%, #d9a946 45%, #7d9bc4 100%);
  }
  .host {
    position: absolute;
    left: 20px;
    top: 900px;
    width: 600px;
    margin: 0;
    text-align: center;
    font-family: "Parisienne", cursive;
    font-size: 34px;
    line-height: 40px;
    color: var(--cream);
    text-shadow: 0 1px 2px rgba(90, 20, 5, 0.5);
  }
  .details {
    position: absolute;
    left: 37px;
    top: 1008px;
    width: 726px;
    height: 178px;
    box-sizing: border-box;
    padding-top: 18px;
    background: linear-gradient(180deg, var(--panel) 0%, var(--panel-edge) 100%);
    text-align: center;
    color: var(--maroon);
    font-size: 34px;
    font-weight: 500;
    line-height: 50px;
    letter-spacing: 2px;
  }
  .details p { margin: 0; }
</style>
</head>
<body>
<main class="poster">
  <div class="backdrop-art" role="img" aria-label="Large faint red folk illustration of a deity with peacock and lotus patterns"></div>

  <h1 class="title">kirtan</h1>

  <svg class="sun-emblem" viewBox="0 0 160 160" role="img" aria-label="Radiant golden sun emblem">
    <defs>
      <radialGradient id="sun-glow" cx="50%" cy="50%" r="50%">
        <stop offset="0%" stop-color="#ffd21a"/>
        <stop offset="70%" stop-color="#ffc20e"/>
        <stop offset="100%" stop-color="#ffb000" stop-opacity="0"/>
      </radialGradient>
    </defs>
    <circle cx="80" cy="80" r="78" fill="url(#sun-glow)"/>
    <circle cx="80" cy="80" r="50" fill="#ffd21a"/>
  </svg>

  <span class="shanti" lang="hi">शान्ति</span>
  <h2 class="subtitle">experience</h2>

  <p class="tagline">An evening of music<br>&amp; singing of sacred</p>
  <span class="tagline-mantras">mantra's</span>

  <div class="photo photo-singer" role="img" aria-label="Photo of a woman singing with eyes closed among a seated audience"></div>
  <div class="photo photo-harmonium" role="img" aria-label="Photo of a woman playing a harmonium"></div>
  <div class="photo photo-chanting" role="img" aria-label="Photo of a man chanting into a microphone outdoors"></div>

  <p class="host">Free Kirtan Experience<br>with Mohan Priya Sevi &amp; Companions</p>

  <section class="details">
    <p>every friday night 7:00pm-8:30pm</p>
    <p>Kealoha Pilates &amp; Movement Studio</p>
    <p>947 Hollister Rd paia</p>
  </section>
</main>
</body>
</html>
```